Probate (Legal) Wordpress Design with Coding for Online Company

I need a Wordpress design with coding, pictures, content to be provided by me, fully responsive, and development. This is for a 6-7 page design.

Pages Needed: Home/About/Probate/Process/FAQ/Contact Us/Blog.

The home page should be organized as followed:
-Steps in Probate: Gather; Implement; Close (each step will come with content)
-Flat-Fee Price & Savings: Content will go here with a button to contact us (phone number) or just the phone number.
-You Have Questions, We Have Answers: five questions with content. Only one question answer to show at a time when clicked on the question from the list.
-Get to Know Us: a brief description with content about what we do and who we are.

Main image slogan: Helping Californians deal with loss with DIGNITY & UNDERSTATING (you may use a better slogan if you wish).

The Contact page should not have a map since we are an online company. We service the entire state of California in every county and city.

The About page should be simple, direct, and easy on the eye. It should have a brief description of who we are and it should have no more than 6 reasons why the client should hire us.

About our online California company. We are not attorneys but legal document assistants who prepare legal documents for probate estate when someone dies with or without a will and assets need to be distributed. We have a flat-fee for Formal Probate of $999 and $699 for Informal Probate. We are an online company and offer our services to the entire state of California in every county. We do everything over the phone and email. The turn around time for us to prepare the initial legal paperwork for the client is within 3-5 business days. We can prepare, file, serve and manage a probate matter from petition to closing. We are not attorneys so our prices are very affordable compare to the attorney.

The company name for the website will be www.velmarhollow.com, The Velmar Hollow Group.

I do not have a logo yet. The colors of the website should be easy on the eye and calming. THE SITE SHOULD BE SIMPLE AND STRAIGHT TO THE POINT. EASY TO NAVIGATE.

The company phone number should be very visible and should stand out to the client. It should also be clickable and ready to dial for smartphone users.

I do not want a contact form on the homepage. THE MAIN THING IS FOR THE POTENTIAL CLIENT TO CALL OUR OFFICE TO SIGN UP.

I do like some images of family or people since we are dealing with people who just lost a loved one. Not all the images have to be of people.

The site should not look like we practice law or that people can mistake us for attorneys.

Target Market(s)

People who just lost a loved one who had property, assets, in California but died with or without a will or trust. This is for people looking to hire non-attorneys.

Coding

Coded - Design and coding required

Font styles to use
Serif

Colors

Designer to choose colors to be used in the design.

Requirements
Must have
• Refer to Project Description.
Nice to have
• The sample images provided is what I am attracted to for the homepage image.
Should not have

```html
<!DOCTYPE html>
<html lang="en">
<head>
<meta charset="utf-8">
<title>Blog – The Velmar Hollow Group</title>
<link rel="stylesheet" href="https://fonts.googleapis.com/css2?family=Crimson+Pro:wght@500;600&family=Lato:wght@400;700&family=Open+Sans:wght@400;600&display=swap">
<style>
:root{
  --teal:#0f6f8c;
  --teal-dark:#0b5d76;
  --orange:#f7941d;
  --orange-deep:#c98020;
  --mist:#e6f1f1;
  --ink:#333;
  --text:#444;
  --white:#fff;
}
*{box-sizing:border-box;margin:0;padding:0}
html,body{width:1200px;height:3087px;overflow:hidden;background:var(--white)}
body{font-family:"Lato",Arial,sans-serif;color:var(--text);position:relative}
a{color:inherit;text-decoration:none}

.site-header{height:126px;position:relative;border-top:4px solid var(--orange)}
.brand{position:absolute;left:99px;top:30px;display:flex;align-items:center;gap:12px}
.brand-mark{width:26px;height:26px;background:var(--orange);border-radius:50%}
.brand-name{font-family:"Crimson Pro",Georgia,serif;font-weight:600;font-size:22px;color:var(--teal);letter-spacing:.5px}
.call-pill{position:absolute;left:792px;top:0;width:299px;height:42px;background:var(--orange);border-radius:0 0 26px 26px;color:var(--white);font-weight:700;font-size:16px;display:flex;align-items:center;justify-content:center;gap:10px}
.main-nav{position:absolute;right:99px;top:78px;display:flex;gap:36px;font-family:"Lato",sans-serif;font-weight:700;font-size:15px;color:var(--ink)}

.page-banner{height:193px;position:relative;background:linear-gradient(90deg,#4d4a46 0%,#6d645c 45%,#8a7a6c 70%,#5f5650 100%)}
.page-banner h1{position:absolute;left:99px;top:62px;font-family:"Crimson Pro",Georgia,serif;font-weight:600;font-size:54px;color:var(--white);letter-spacing:1px}

.post{position:relative}
.post.alt{background:var(--mist)}
.post-photo{position:absolute;width:416px;height:309px;border-radius:3px}
.post-body{position:absolute;width:558px}
.post-title{font-family:"Crimson Pro",Georgia,serif;font-weight:600;font-size:23px;color:var(--teal);letter-spacing:.5px;text-transform:uppercase}
.post-title::after{content:"";display:block;width:94px;height:2px;background:var(--teal);margin-top:14px}
.post-body p{font-family:"Open Sans",Arial,sans-serif;font-size:13.6px;line-height:22px;color:var(--text);margin-top:20px}
.post-body p + p{margin-top:10px}
.btn-read{display:inline-block;margin-top:26px;background:var(--orange);color:var(--white);font-weight:700;font-size:15px;padding:0 0;width:111px;height:50px;line-height:50px;text-align:center}

.pagination{height:146px;display:flex;align-items:center;justify-content:center;gap:11px}
.page-link{width:49px;height:41px;border:2px solid #555;border-radius:4px;display:flex;align-items:center;justify-content:center;font-family:"Open Sans",sans-serif;font-size:22px;color:#333}
.page-link.current{background:var(--teal);border-color:var(--teal);color:var(--white)}
.page-arrow{width:30px;display:flex;justify-content:center}

.intro-band{height:488px;display:flex}
.intro-col{width:600px;position:relative;color:var(--white);padding:56px 0 0 99px}
.intro-col.what{background:linear-gradient(135deg,#1a86a6 0%,#157792 50%,#0f6780 100%)}
.intro-col.who{background:linear-gradient(135deg,#d48f2c 0%,#c47d1f 55%,#a9691a 100%);padding-left:33px}
.intro-col h2{font-family:"Crimson Pro",Georgia,serif;font-weight:600;font-size:33px;letter-spacing:.5px}
.intro-col h2::after{content:"";display:block;width:104px;height:2px;background:var(--white);margin-top:14px}
.intro-col p{font-family:"Open Sans",sans-serif;font-weight:600;font-size:13.6px;line-height:22px;width:470px;margin-top:24px}
.intro-col p + p{margin-top:14px}
.btn-outline{display:inline-block;margin-top:34px;width:113px;height:54px;line-height:50px;border:2px solid var(--white);text-align:center;font-weight:700;font-size:15px}
.dash{position:absolute;left:240px;bottom:92px;width:150px;border-top:1px dashed rgba(255,255,255,.5)}

.site-footer{position:relative;height:298px}
.footer-nav{position:absolute;top:70px;left:0;width:1200px;display:flex;justify-content:center;font-family:"Open Sans",sans-serif;font-size:15px;color:#222}
.footer-nav span.sep{margin:0 22px}
.contact-row{position:absolute;top:130px;left:0;width:1200px;display:flex;justify-content:center;gap:54px;font-family:"Open Sans",sans-serif;font-size:21px;color:#222}
.contact-item{display:flex;align-items:center;gap:14px}
.icon-ring{width:44px;height:44px;border:2px solid #222;border-radius:50%;display:flex;align-items:center;justify-content:center}
.footer-rule{position:absolute;top:213px;left:99px;width:1002px;border-top:2px solid #333}
.copyright{position:absolute;top:240px;left:0;width:1200px;text-align:center;font-family:"Open Sans",sans-serif;font-size:15px;color:#222}
</style>
</head>
<body>

<header class="site-header">
  <a class="brand" href="#"><span class="brand-mark"></span><span class="brand-name">The Velmar Hollow Group</span></a>
  <a class="call-pill" href="tel:+1805550147">
    <svg width="16" height="16" viewBox="0 0 16 16"><rect x="0" y="0" width="16" height="16" rx="3" fill="#fff"/><path d="M5 3.5l1.6 2.2-1 1c.6 1.3 1.5 2.2 2.8 2.8l1-1 2.2 1.6-.8 1.6C8 11.8 4.2 8 4.1 4.3z" fill="#f7941d"/></svg>
    Call Us At: +180 555 0147
  </a>
  <nav class="main-nav"><a href="#">HOME</a><a href="#">ABOUT</a><a href="#">PROBATE</a><a href="#">PROCESS</a><a href="#">FAQ</a><a href="#">CONTACT US</a><a href="#">BLOG</a></nav>
</header>

<section class="page-banner" role="img" aria-label="Family photograph of a mother and daughter, darkened behind the page title">
  <h1>BLOG</h1>
</section>

<article class="post" style="height:484px">
  <div class="post-body" style="left:99px;top:110px">
    <h2 class="post-title">Nemo enim ipsam voluptatem</h2>
    <p>About our online California company. We are not attorneys but legal document assistants who prepare legal documents for probate estate when someone dies with or without a will and assets need to be distributed.</p>
    <p>The turn around time for us to prepare the initial legal paperwork for the client is within 3-5 business days. We can prepare, file, serve and manage a probate matter from petition to closing.</p>
    <a class="btn-read" href="#">READ MORE</a>
  </div>
  <div class="post-photo" style="left:685px;top:101px;background:linear-gradient(135deg,#b7bcb0 0%,#8c7a66 45%,#5a9a58 75%,#3d6e4a 100%)" role="img" aria-label="Photo of a mother comforting her young son"></div>
</article>

<article class="post alt" style="height:444px">
  <div class="post-photo" style="left:99px;top:70px;background:linear-gradient(135deg,#2f3a3c 0%,#4d4a48 45%,#c9c7c2 80%,#e2e0dc 100%)" role="img" aria-label="Photo of a distressed woman holding her head"></div>
  <div class="post-body" style="left:542px;top:50px">
    <h2 class="post-title">Magni dolores eos qui</h2>
    <p>About our online California company. We are not attorneys but legal document assistants who prepare legal documents for probate estate when someone dies with or without a will and assets need to be distributed.</p>
    <p>The turn around time for us to prepare the initial legal paperwork for the client is within 3-5 business days. We can prepare, file, serve and manage a probate matter from petition to closing.</p>
    <a class="btn-read" href="#">READ MORE</a>
  </div>
</article>

<article class="post" style="height:463px">
  <div class="post-body" style="left:99px;top:90px">
    <h2 class="post-title">Ratione voluptatem sequi</h2>
    <p>About our online California company. We are not attorneys but legal document assistants who prepare legal documents for probate estate when someone dies with or without a will and assets need to be distributed.</p>
    <p>The turn around time for us to prepare the initial legal paperwork for the client is within 3-5 business days. We can prepare, file, serve and manage a probate matter from petition to closing.</p>
    <a class="btn-read" href="#">READ MORE</a>
  </div>
  <div class="post-photo" style="left:685px;top:80px;background:linear-gradient(90deg,#8a8d98 0%,#6b6e7c 45%,#3e5a86 65%,#d9b51e 85%,#e3c22a 100%)" role="img" aria-label="Photo of a small boy hugging an adult"></div>
</article>

<article class="post alt" style="height:445px">
  <div class="post-photo" style="left:99px;top:70px;background:linear-gradient(135deg,#6e6e6e 0%,#3a3a3a 40%,#1e1e1e 70%,#4a4a4a 100%)" role="img" aria-label="Photo of a mother embracing her daughter"></div>
  <div class="post-body" style="left:542px;top:50px">
    <h2 class="post-title">Numquam eius modi tempora</h2>
    <p>About our online California company. We are not attorneys but legal document assistants who prepare legal documents for probate estate when someone dies with or without a will and assets need to be distributed.</p>
    <p>The turn around time for us to prepare the initial legal paperwork for the client is within 3-5 business days. We can prepare, file, serve and manage a probate matter from petition to closing.</p>
    <a class="btn-read" href="#">READ MORE</a>
  </div>
</article>

<nav class="pagination" aria-label="Blog pages">
  <span class="page-arrow"><svg width="24" height="22" viewBox="0 0 24 22"><path d="M11 2L2 11l9 9M3 11h19" stroke="#555" stroke-width="4" fill="none"/></svg></span>
  <a class="page-link" href="#">1</a>
  <a class="page-link current" href="#">2</a>
  <a class="page-link" href="#">3</a>
  <a class="page-link" href="#">4</a>
  <a class="page-link" href="#">5</a>
  <span class="page-arrow"><svg width="24" height="22" viewBox="0 0 24 22"><path d="M13 2l9 9-9 9M21 11H2" stroke="#555" stroke-width="4" fill="none"/></svg></span>
</nav>

<section class="intro-band">
  <div class="intro-col what" role="img" aria-label="Teal-toned photo of hands working with documents">
    <h2>WHAT WE DO</h2>
    <p>Sed ut perspiciatis unde omnis iste natus error sit voluptatem accusantium doloremque laudantium, totam rem aperiam, eaque ipsa quae ab illo inventore veritatis et quasi architecto beatae.</p>
    <p>Nemo enim ipsam voluptatem quia voluptas sit aspernatur aut odit aut fugit, sed quia consequuntur magni dolores eos qui ratione voluptatem.</p>
    <a class="btn-outline" href="#">READ MORE</a>
    <span class="dash"></span>
  </div>
  <div class="intro-col who" role="img" aria-label="Amber-toned photo of a hand signing a paper">
    <h2>WHO WE ARE</h2>
    <p>Sed ut perspiciatis unde omnis iste natus error sit voluptatem accusantium doloremque laudantium, totam rem aperiam, eaque ipsa quae ab illo inventore veritatis et quasi architecto beatae.</p>
    <p>Nemo enim ipsam voluptatem quia voluptas sit aspernatur aut odit aut fugit, sed quia consequuntur magni dolores eos qui ratione voluptatem.</p>
    <a class="btn-outline" href="#">READ MORE</a>
  </div>
</section>

<footer class="site-footer">
  <nav class="footer-nav">
    <a href="#">HOME</a><span class="sep">|</span><a href="#">ABOUT</a><span class="sep">|</span><a href="#">PROBATE</a><span class="sep">|</span><a href="#">PROCESS</a><span class="sep">|</span><a href="#">FAQ</a><span class="sep">|</span><a href="#">CONTACT US</a><span class="sep">|</span><a href="#">BLOG</a>
  </nav>
  <div class="contact-row">
    <a class="contact-item" href="tel:+1805550147"><span class="icon-ring"><svg width="20" height="20" viewBox="0 0 16 16"><path d="M3.5 1.5l2.3 3-1.3 1.4c.8 1.8 2.1 3.1 3.9 3.9l1.4-1.3 3 2.3-1.1 2.3C6.5 13 2.9 9.4 1.2 2.6z" fill="#222"/></svg></span>+180 555 0147</a>
    <a class="contact-item" href="mailto:info@velmarhollow.com"><span class="icon-ring"><svg width="22" height="16" viewBox="0 0 22 16"><rect x="1" y="1" width="20" height="14" rx="2" fill="none" stroke="#222" stroke-width="2"/><path d="M2 2l9 7 9-7" fill="none" stroke="#222" stroke-width="2"/></svg></span>info@velmarhollow.com</a>
  </div>
  <div class="footer-rule"></div>
  <p class="copyright">Copyrights @ 2017 The Velmar Hollow Group. All Rights Reserved.</p>
</footer>

</body>
</html>
```